Marwick Law Letterhead

We need a new letterhead design for a Law Firm. The address for the law firm is 1475 Calloway Street, Suite 210, Houston, Texas 77041. Phone Number: 832-361-9027; Fax Number: 832-614-7359. The logo is uploaded to the project.

```html
<!DOCTYPE html>
<html lang="en">
<head>
<meta charset="utf-8">
<title>Marwick Law Letterhead</title>
<link href="https://fonts.googleapis.com/css2?family=Montserrat:wght@400;500;600&display=swap" rel="stylesheet">
<style>
:root{
  --bg:#e8e8e8;
  --paper:#ffffff;
  --navy:#1c2d5e;
  --red:#e31b23;
  --red-dark:#6e0a10;
  --ink:#2a2a2a;
  --ink-strong:#111111;
}
*{margin:0;padding:0;box-sizing:border-box}
html,body{width:1154px;height:1200px;overflow:hidden;background:var(--bg)}
body{font-family:"Montserrat",sans-serif;color:var(--ink)}
.letterhead{
  position:absolute;left:162px;top:20px;width:830px;height:1160px;
  background:var(--paper);box-shadow:0 4px 18px rgba(0,0,0,.18);
}
.brand{position:absolute;left:34px;top:78px;display:flex;align-items:center;gap:12px}
.brand-mark{width:46px;height:46px;background:var(--navy)}
.brand-name{font-size:34px;font-weight:600;color:var(--navy);letter-spacing:.5px;line-height:1}
.contact{
  position:absolute;left:620px;top:62px;padding-left:13px;
  border-left:1.5px solid var(--red);font-size:14px;line-height:18px;color:var(--ink-strong)
}
.contact address{font-style:normal;margin-bottom:11px}
.contact-line{display:flex;align-items:center;gap:9px;height:21px}
.contact-line svg{width:13px;height:13px;fill:var(--red)}
.rule{position:absolute;left:30px;top:198px;width:768px;height:2px;background:var(--red)}
.rule-bar{
  position:absolute;left:287px;top:192px;width:273px;height:11px;
  background:linear-gradient(90deg,var(--red),var(--red-dark))
}
.recipient{position:absolute;left:31px;top:266px;font-size:13.3px;line-height:20.6px;color:var(--ink-strong)}
.body{position:absolute;left:33px;top:353px;width:768px;font-size:13.3px;line-height:20.6px;text-align:justify}
.body p{margin-bottom:20.6px}
.closing{position:absolute;left:30px;top:936px;font-size:16px;color:var(--ink-strong)}
.signature{position:absolute;left:28px;top:962px;width:94px;height:32px;background:linear-gradient(90deg,#d9d9d9,#efefef);border-radius:3px}
</style>
</head>
<body>
<main class="letterhead">
  <header>
    <div class="brand">
      <span class="brand-mark"></span>
      <span class="brand-name">Marwick Law</span>
    </div>
    <div class="contact">
      <address>1475 Calloway Street,<br>Suite 210, Houston,<br>Texas 77041</address>
      <div class="contact-line">
        <svg viewBox="0 0 24 24" aria-hidden="true"><path d="M6.6 10.8a15.1 15.1 0 0 0 6.6 6.6l2.2-2.2a1 1 0 0 1 1-.25 11.4 11.4 0 0 0 3.6.57 1 1 0 0 1 1 1V20a1 1 0 0 1-1 1A17 17 0 0 1 3 4a1 1 0 0 1 1-1h3.5a1 1 0 0 1 1 1c0 1.25.2 2.45.57 3.57a1 1 0 0 1-.25 1z"/></svg>
        <span>832-361-9027</span>
      </div>
      <div class="contact-line">
        <svg viewBox="0 0 24 24" aria-hidden="true"><path d="M7 3h10v4H7zM4 8h16a2 2 0 0 1 2 2v6h-4v5H6v-5H2v-6a2 2 0 0 1 2-2zm4 8v3h8v-3z"/></svg>
        <span>832-614-7359</span>
      </div>
    </div>
    <div class="rule"></div>
    <div class="rule-bar"></div>
  </header>

  <div class="recipient">Mr/s<br>First Name and Last Name<br>Company Name<br>Address</div>

  <section class="body">
    <p>Lorem ipsum dolor sit amet,consectetur adipiscing sed do eiusmod tempor incididunt laboreet dolore magna aliqua.Ut enim ad minim.veniam, quis nostrud exercitation ullamco laboris nisi ut aliquip exea commodo consequat.Lorem ipsum dolor sit amet,consectetur adipiscing sed do eiusmod tempor incididunt.labore et dolore magna aliqua. Ut enim</p>
    <p>Lorem ipsum dolor sit amet, consectetur adipiscing sed do eiusmod tempor incididunt labore et dolore magna aliqua. Ut enim ad minim veniam, quis nostrud exercitation ullamco laboris nisi ut aliquip exea commodo consequat.Duis aute irure dolor in reprehenderit in voluptate velit esse cillum irure dolor in reprehenderit in voluptate velit esse irure</p>
    <p>Lorem ipsum dolor sit amet, consectetur adipiscing sed do eiusmod tempor incididunt labore et dolore magna aliqua. consequat. Duis aute irure dolor in.reprehenderit in voluptate velit esse cillum dolore eu fugiat nulla pariatur. Excepteur sint occaecat cupidatat non proident, sunt in culpa qui officia deserunt mollit,</p>
    <p>Lorem ipsum dolor sit amet, consectetur adipiscing sed do eiusmod tempor incididunt labore et dolore magna aliqua. Ut enim Lorem ipsum dolor sit amet, consectetur adipiscing sed do eiusmod tempor incididunt labore et dolore magna aliqua. Ut enim Lorem ipsum aliqua.ipsum</p>
    <p>Lorem ipsum dolor sit amet, consectetur adipiscing sed do eiusmod tempor incididunt labore et dolore magna aliqua. Ut enim ad minim veniam, quis nostrud exercitation ullamco laboris nisi ut aliquip exea commodo consequat.Duis aute irure dolor in reprehenderit in voluptate velit esse cillum irure dolor in reprehenderit in voluptate velit esse irure</p>
    <p>Lorem ipsum dolor sit amet, consectetur adipiscing sed do eiusmod tempor incididunt labore et dolore magna aliqua. Ut enim ad minim veniam, quis nostrud exercitation ullamco laboris nisi ut aliquip exea commodo consequat.Duis aute irure dolor in reprehenderit in voluptate velit esse cillum irure dolor in reprehenderit in voluptate velit esse irure</p>
  </section>

  <div class="closing">Regards</div>
  <div class="signature" role="img" aria-label="Handwritten signature"></div>
</main>
</body>
</html>
```